Social Media App Needs PPT Template

We need a PowerPoint template for a new social media company based in the DC area called "Bold Ledger." We provide an interactive digital platform for executives to share actionable advice. We would like to see designs that use our orange logo color as an accent, but are mainly grey, white, and black. The final design should communicate clean, chic, modern, and professional.

Target Market(s)

Executives

Industry/Entity Type

Information Technology

Font styles to use
Sans Serif

Colors
f78f20
fbe7d2
ffffff
000000
e8e8e8
757575

Requirements
Must have
• My project must have title page and many options for the body of the ppt (graphs, tables, etc). It also needs to be easy to modify. I must have someone who is experienced in creating powerpoint templates.
Nice to have
• It would be nice to have a very modern and clean design that includes the logo on every page, but still leaves a lot of room for the content of the slide
Should not have
• My design project should not look to busy.

```html
<!DOCTYPE html>
<html lang="en">
<head>
<meta charset="utf-8">
<title>Bold Ledger – About Our Company</title>
<link href="https://fonts.googleapis.com/css2?family=Lato:wght@300;400;700&display=swap" rel="stylesheet">
<style>
  :root {
    --stage: #909090;
    --orange: #e8871c;
    --orange-bar: #f0901e;
    --charcoal: #474747;
    --slate: #6b6b6d;
    --ink: #555555;
    --axis: #8a8a8a;
    --white: #ffffff;
  }
  html, body {
    margin: 0;
    width: 1200px;
    height: 960px;
    overflow: hidden;
    background: var(--stage);
    font-family: "Lato", sans-serif;
  }
  .slide {
    position: absolute;
    left: 87px;
    top: 128px;
    width: 1046px;
    height: 784px;
    background: radial-gradient(ellipse at 55% 35%, #ffffff 0%, #f7f7f7 45%, #eeeeee 100%);
    overflow: hidden;
  }
  .slide-shapes {
    position: absolute;
    left: 0;
    top: 0;
  }
  .slide-title {
    position: absolute;
    left: 32px;
    top: 68px;
    margin: 0;
    font-weight: 300;
    font-size: 39px;
    color: var(--white);
    letter-spacing: 0.2px;
  }
  .brand {
    position: absolute;
    left: 852px;
    top: 74px;
    display: flex;
    align-items: center;
    gap: 8px;
    font-weight: 700;
    font-size: 22px;
    color: var(--white);
  }
  .brand-dot {
    width: 20px;
    height: 20px;
    border-radius: 50%;
    background: var(--orange-bar);
  }
  .legend {
    position: absolute;
    left: 917px;
    top: 214px;
    margin: 0;
    padding: 0;
    list-style: none;
    font-size: 20px;
    color: var(--ink);
  }
  .legend li {
    display: flex;
    align-items: center;
    gap: 6px;
    height: 28px;
  }
  .legend .swatch { width: 11px; height: 11px; }
  .swatch.s1 { background: var(--orange-bar); }
  .swatch.s2 { background: var(--charcoal); }
  .swatch.s3 { background: var(--slate); }
  .body-copy {
    position: absolute;
    left: 53px;
    top: 570px;
    width: 949px;
    margin: 0;
    font-size: 18.2px;
    line-height: 26.4px;
    color: var(--ink);
    text-align: justify;
  }
  .footer-text {
    position: absolute;
    left: 28px;
    top: 748px;
    font-size: 13.6px;
    color: #e6e6e6;
  }
  .chart-label { font-family: "Lato", sans-serif; fill: var(--ink); }
</style>
</head>
<body>
<section class="slide">
  <svg class="slide-shapes" width="1046" height="784" viewBox="0 0 1046 784">
    <!-- header -->
    <polygon points="823,34 1046,34 1046,44 813,44" fill="var(--orange)"/>
    <polygon points="0,49 790,49 705,131 0,131" fill="var(--orange)"/>
    <polygon points="630,49 790,49 755,82 580,82" fill="#ef9630" opacity="0.5"/>
    <polygon points="800,49 1046,49 1046,131 715,131" fill="var(--charcoal)"/>
    <polygon points="0,136 712,136 703,145 0,145" fill="var(--charcoal)"/>

    <!-- chart grid -->
    <g stroke="var(--axis)" stroke-width="1" stroke-dasharray="8 6">
      <line x1="90" y1="228" x2="865" y2="228"/>
      <line x1="90" y1="280" x2="865" y2="280"/>
      <line x1="90" y1="333" x2="865" y2="333"/>
      <line x1="90" y1="385" x2="865" y2="385"/>
      <line x1="90" y1="438" x2="865" y2="438"/>
    </g>
    <g stroke="var(--axis)" stroke-width="1.2">
      <line x1="85" y1="226" x2="85" y2="490"/>
      <line x1="80" y1="490" x2="865" y2="490"/>
    </g>

    <!-- bars -->
    <g>
      <rect x="129" y="265" width="51" height="225" fill="var(--orange-bar)"/>
      <rect x="180" y="309" width="51" height="181" fill="var(--charcoal)"/>
      <rect x="231" y="283" width="51" height="207" fill="var(--slate)"/>

      <rect x="369" y="296" width="51" height="194" fill="var(--orange-bar)"/>
      <rect x="420" y="262" width="51" height="228" fill="var(--charcoal)"/>
      <rect x="471" y="312" width="51" height="178" fill="var(--slate)"/>

      <rect x="601" y="325" width="51" height="165" fill="var(--orange-bar)"/>
      <rect x="652" y="275" width="51" height="215" fill="var(--charcoal)"/>
      <rect x="703" y="257" width="51" height="233" fill="var(--slate)"/>
    </g>

    <!-- axis labels -->
    <g class="chart-label" font-size="18" text-anchor="middle">
      <text x="62" y="234">5</text>
      <text x="62" y="287">4</text>
      <text x="62" y="339">3</text>
      <text x="62" y="392">2</text>
      <text x="62" y="444">1</text>
      <text x="62" y="497">0</text>
      <text x="201" y="527">Category 1</text>
      <text x="441" y="527">Category 2</text>
      <text x="682" y="527">Category 3</text>
    </g>

    <!-- footer -->
    <polygon points="0,742 299,742 267,773 0,773" fill="var(--charcoal)"/>
    <polygon points="307,742 1046,742 1046,773 275,773" fill="var(--orange)"/>
  </svg>

  <h1 class="slide-title">About Our Company</h1>
  <div class="brand"><span class="brand-dot"></span>Bold Ledger</div>

  <ul class="legend">
    <li><span class="swatch s1"></span>Series 1</li>
    <li><span class="swatch s2"></span>Series 2</li>
    <li><span class="swatch s3"></span>Series 3</li>
  </ul>

  <p class="body-copy">Duis autem vel eum iriure dolor in hendrerit in vulputate velit esse molestie consequat, vel illum dolore eu feugiat nulla facilisis at vero eros et accumsan et iusto odio dignissim qui blandit praesent luptatum zzril delenit augue duis dolore te feugait nulla facilisi. Nam liber tempor cum soluta nobis eleifend option congue nihil imperdiet doming id quod mazim placerat facer possim assum.</p>

  <div class="footer-text">www.boldledger.com&nbsp;&nbsp;|&nbsp;&nbsp;Page 4</div>
</section>
</body>
</html>
```